Equipment Finance Specialist I work with companies who need the funds to buy their equipment

I would like a business card that stands out on the shelves. I want to be able to hand it to someone and say WOW. This card should have my logo.
You can put color into it I am very open on design and color

What my company does is we deal with dealerships that sell equipment such as Dump Trucks garbage trucks tractors trailers. Customers get referred to us and depending on their time in business we will ask for the following items

Companies that have been in business for more than two years we have a credit application program up to 250K . With this program we need the following items Credit application filled out(which is what I would like to be able for the customer to click on my website to get.) as well as three current month bank statements.

Deals over 250k we will need the following items

2 years business tax returns
2 years personal tax returns
Profit & Loss statement
Personal Financial Statement

what we do
100% FINANCING
SEASONAL PAYMENTS
LOAN BALLOON PAYMENTS
TRAC LEASING
LOW-INTEREST REFINANCING RATES
DEBT CONSOLIDATION

We specialize in creative financing solutions and offer a variety of reliable, flexible and expandable lending choices.

Target Market(s)

Trucking Companies

Industry/Entity Type

Trucking Company

Contact Information for Business Card

* $250,000 Application only Program
* Loans from $30,000 to 5,000,000
* Competitive Interest Rates

Font styles to use
Serif
Sans Serif

Colors

Designer to choose colors to be used in the design.

Requirements
Must have
• On the back of the card.
• * $250,000 Application only Program
• * Loans from $30,000 to 5,000,000
• My name, email, website. address
• * Competitive Interest Rates
• * 100% Financing
Nice to have
• I want my logo to pop on the card
• My logo is the great one I would like to use
Should not have
• I am up for your creativity as well

```html
<!DOCTYPE html>
<html lang="en">
<head>
<meta charset="utf-8">
<title>Truckline Capital – Business Card</title>
<link rel="stylesheet" href="https://fonts.googleapis.com/css2?family=Open+Sans:wght@400;600;700;800&display=swap">
<style>
  :root {
    --bg: #3a322d;
    --card: #1b1d1f;
    --card-edge: #25282a;
    --ink: #ffffff;
    --silver: #c9cccf;
    --silver-dark: #8d9296;
    --muted: #d8d8d8;
  }
  * { box-sizing: border-box; margin: 0; padding: 0; }
  html, body {
    width: 1200px; height: 864px; overflow: hidden;
    background: var(--bg);
    font-family: "Open Sans", Arial, sans-serif;
  }
  .canvas {
    width: 1200px; height: 864px;
    display: flex; align-items: center; justify-content: center; gap: 40px;
  }
  .card {
    width: 540px; height: 309px;
    background: linear-gradient(160deg, var(--card-edge), var(--card) 55%);
    position: relative;
    box-shadow: 0 14px 30px rgba(0,0,0,.45);
    color: var(--ink);
  }

  /* Back of card */
  .card-back { display: flex; flex-direction: column; align-items: center; }
  .back-mark {
    margin-top: 52px;
    display: flex; align-items: center; gap: 12px;
  }
  .back-mark .dot {
    width: 96px; height: 96px; border-radius: 50%;
    background: radial-gradient(circle at 35% 30%, var(--silver), var(--silver-dark));
  }
  .back-mark .brand {
    font-weight: 800; font-size: 26px; line-height: 1.05;
    color: var(--silver); text-transform: uppercase;
  }
  .offers {
    position: absolute; bottom: 44px; left: 0; right: 0;
    text-align: center; font-size: 14.5px; line-height: 1.35; color: var(--muted);
  }

  /* Front of card */
  .card-front { display: flex; align-items: center; }
  .logo {
    width: 275px; display: flex; align-items: center; justify-content: center; gap: 10px;
  }
  .logo .dot {
    width: 46px; height: 46px; border-radius: 50%; background: var(--ink); flex: none;
  }
  .logo .brand {
    font-weight: 800; font-size: 25px; line-height: 1.02; text-transform: uppercase; color: var(--ink);
  }
  .divider {
    width: 1px; height: 170px;
    background: linear-gradient(to bottom, transparent, var(--silver-dark) 20%, var(--silver-dark) 80%, transparent);
  }
  .details { padding-left: 26px; font-size: 15px; line-height: 1.3; }
  .person-name { font-weight: 700; font-size: 19px; letter-spacing: .5px; }
  .person-title { font-size: 13px; letter-spacing: .5px; margin-bottom: 14px; }
  .address { margin-bottom: 8px; }
  .contact { list-style: none; }
  .contact li { display: flex; align-items: center; gap: 10px; }
  .contact svg { width: 13px; height: 13px; fill: var(--ink); flex: none; }
</style>
</head>
<body>
<main class="canvas">
  <section class="card card-back" aria-label="Card back">
    <div class="back-mark">
      <span class="dot"></span>
      <span class="brand">Truckline<br>Capital</span>
    </div>
    <p class="offers">
      $250,000 Application only Program &bull; Loans from $30,000 to 5,000,000<br>
      Competitive Interest Rates &bull; 100% Financing
    </p>
  </section>

  <section class="card card-front" aria-label="Card front">
    <div class="logo">
      <span class="dot"></span>
      <span class="brand">Truckline<br>Capital</span>
    </div>
    <div class="divider"></div>
    <div class="details">
      <p class="person-name">MARK ELLISON</p>
      <p class="person-title">PRESIDENT</p>
      <p class="address">2190 Harbor Lane<br>Linwood, NY 11020</p>
      <ul class="contact">
        <li><svg viewBox="0 0 16 16"><path d="M3 1h3l1.5 4-2 1.2a9 9 0 0 0 4.3 4.3L11 8.5l4 1.5v3a2 2 0 0 1-2 2A12 12 0 0 1 1 3a2 2 0 0 1 2-2z"/></svg>555 0142 3386</li>
        <li><svg viewBox="0 0 16 16"><path d="M1 3h14v10H1z M1 3l7 6 7-6" fill="none" stroke="#fff" stroke-width="1.6"/></svg>mark@trucklinecapital.com</li>
        <li><svg viewBox="0 0 16 16"><circle cx="8" cy="8" r="7"/></svg>www.trucklinecapital.com</li>
      </ul>
    </div>
  </section>
</main>
</body>
</html>
```